Company director needs a business card design

I am a semi-retired former senior finance executive who sits on a number of public and private company boards and do some consulting work. I work largely with emerging businesses but deal regularly with top end of town lawyers, bankers etc. I need a thoughtful but relatively conservative design which would also resonate with my younger client base. Some colour would be good. Information limited to name, address, office tel, mobile and email.

Finance

```html
<!DOCTYPE html>
<html lang="en">
<head>
<meta charset="utf-8">
<title>Marcus Hale – Business Card</title>
<link rel="stylesheet" href="https://fonts.googleapis.com/css2?family=Michroma&family=Exo+2:wght@400&display=swap">
<style>
  :root {
    --backdrop: #e9e7e3;
    --card: #ffffff;
    --accent: #e8214a;
    --ink: #2e2e2e;
    --ink-soft: #555555;
  }
  * { margin: 0; padding: 0; box-sizing: border-box; }
  html, body {
    width: 1200px;
    height: 800px;
    overflow: hidden;
    background: var(--backdrop);
  }
  .business-card {
    position: absolute;
    left: 180px;
    top: 160px;
    width: 840px;
    height: 480px;
    background: var(--card);
    box-shadow: 0 10px 30px rgba(0,0,0,0.18);
    overflow: hidden;
  }
  .accent-band {
    position: absolute;
    left: 0;
    bottom: 0;
    width: 840px;
    height: 40px;
  }
  .identity {
    position: absolute;
    right: 56px;
    top: 120px;
    text-align: right;
  }
  .identity__name {
    font-family: "Michroma", sans-serif;
    font-size: 30px;
    letter-spacing: 1px;
    color: var(--accent);
    font-weight: 400;
    line-height: 1.1;
  }
  .identity__title {
    margin-top: 8px;
    font-family: "Exo 2", sans-serif;
    font-size: 16px;
    letter-spacing: 1.2px;
    color: var(--ink-soft);
  }
  .contact-list {
    position: absolute;
    right: 56px;
    top: 278px;
    list-style: none;
  }
  .contact-list__item {
    display: flex;
    align-items: center;
    justify-content: flex-end;
    gap: 18px;
    height: 32px;
    font-family: "Michroma", sans-serif;
    font-size: 16px;
    color: var(--ink);
    letter-spacing: 0.5px;
    white-space: nowrap;
  }
  .contact-list__item--address {
    font-family: "Exo 2", sans-serif;
    font-size: 18px;
    letter-spacing: 1px;
  }
  .contact-list__icon {
    width: 20px;
    height: 20px;
    flex: none;
  }
</style>
</head>
<body>
  <article class="business-card">
    <header class="identity">
      <h1 class="identity__name">MARCUS HALE</h1>
      <p class="identity__title">Managing Director</p>
    </header>

    <ul class="contact-list">
      <li class="contact-list__item">
        <span>0098 7654 321</span>
        <svg class="contact-list__icon" viewBox="0 0 20 20" aria-hidden="true">
          <rect x="4" y="2" width="12" height="16" rx="2" fill="none" stroke="var(--accent)" stroke-width="2"/>
        </svg>
      </li>
      <li class="contact-list__item">
        <span>0098 7654 320</span>
        <svg class="contact-list__icon" viewBox="0 0 20 20" aria-hidden="true">
          <rect x="4" y="2" width="12" height="17" fill="var(--accent)"/>
          <g fill="#fff">
            <rect x="6" y="4" width="2" height="2"/><rect x="9" y="4" width="2" height="2"/><rect x="12" y="4" width="2" height="2"/>
            <rect x="6" y="8" width="2" height="2"/><rect x="9" y="8" width="2" height="2"/><rect x="12" y="8" width="2" height="2"/>
            <rect x="6" y="12" width="2" height="2"/><rect x="12" y="12" width="2" height="2"/>
            <rect x="9" y="14" width="2" height="5"/>
          </g>
        </svg>
      </li>
      <li class="contact-list__item">
        <span>info@marcushale.com</span>
        <svg class="contact-list__icon" viewBox="0 0 20 20" aria-hidden="true">
          <rect x="1" y="4" width="18" height="12" fill="var(--accent)"/>
          <path d="M1 4 L10 11 L19 4" fill="none" stroke="#fff" stroke-width="1.6"/>
        </svg>
      </li>
      <li class="contact-list__item contact-list__item--address">
        <span>Suite 4, 18 Harbour Lane Brookfield, ST 40210</span>
        <svg class="contact-list__icon" viewBox="0 0 20 20" aria-hidden="true">
          <path d="M10 2 L1 10 L4 10 L4 18 L8 18 L8 13 L12 13 L12 18 L16 18 L16 10 L19 10 Z" fill="var(--accent)"/>
        </svg>
      </li>
    </ul>

    <svg class="accent-band" viewBox="0 0 840 40" preserveAspectRatio="none" aria-hidden="true">
      <path d="M0 26 H290 V22 Q290 12 302 12 H840 V40 H0 Z" fill="var(--accent)"/>
    </svg>
  </article>
</body>
</html>
```